Stylist/Barber Standup Sign for Hair Regrowth Company

We want to design an attractive and eye-catching sign for hair stylists and barbers to sit on their workstations to attract the attention of their clients regarding hair loss and encourage them to speak to their stylist about it of they are would like to seek treatment.
50% of men and 25% of women suffer from hair loss but most are in denial that it is happening or too embarrassed to talk about it.

Copy for the flyer is as follows:

[Section 1:]
This flyer has been placed here/designed to spark conversation about hair loss

[Section 2:]
The truth is...
73% of people believe their hair is thinning
They are right

[Section 3:]
If you've got questions, your stylist or barber has answers.

Additional Background Information:

Primary target audience is men between the ages of 25-45, secondary target audience is men 46-60

Current Consumer Perception? (in the first person) “I’ve been thinking about my hair. I think it’s getting thinner and I’m scared, worried and don’t know what to do. But I don’t know if there is anything that really works. I’ve tried other things and nothing‘s worked.”

Tonality of materials? Very guy friendly, matter of fact, authoritative, its what you might hear from your best friend. Confident. Encouraging, but with a sense of urgency.

Please use our brand colors, but do not include our logo or brand name.
Colors are as follows:
Green: #4ca26f
Light Grey: #999999
Dark Grey: #262626

I have attached print templates in both PDF and Jpeg, please use those to provide final ready to print documents if you are selected.

Target Market(s)

Industry/Entity Type

Health And Wellness

Font styles to use
Sans Serif

Colors
00a990
ffffff
333333
cbcbcb

Requirements
Must have
• We want to get across the following messaging. Ideally you will submit a design using our copy and if you think you can do better, please feel free to submit another design with your own copy/messaging. If you can do it better we would love to select you :-)
• Our copy?
• This flyer has been placed here/designed to spark conversation about hair loss
• The truth is...
• 73% of people believe their hair is thinning
• They are right
• If you've got questions, your stylist or barber has answers
• Also please use our brand colors:
• Green: #4ca26f
• Light Grey: #999999
• Dark Grey: #262626
Should not have
• dont add any logos, images or ornate design. this needs to be simple, easy to ready and eye catching.
• do not use the color red in any capacity.

```html
<!DOCTYPE html>
<html lang="en">
<head>
<meta charset="utf-8">
<title>Hair Loss Conversation Sign</title>
<link rel="stylesheet" href="https://fonts.googleapis.com/css2?family=Montserrat:wght@600;700&family=Lato:wght@300;400;700&display=swap">
<style>
  :root {
    --green: #4ca26f;
    --dark: #262626;
    --light: #e2e3e5;
    --paper: #ffffff;
    --ink: #222222;
    --rule: #555555;
  }
  * { margin: 0; padding: 0; box-sizing: border-box; }
  html, body { width: 902px; height: 1200px; overflow: hidden; background: var(--paper); }
  .sign {
    width: 902px; height: 1200px;
    padding: 27px 31px;
    background: var(--paper);
  }
  .sign-inner {
    width: 840px; height: 1146px;
    background: var(--light);
    display: flex; flex-direction: column;
  }
  .stats {
    position: relative; height: 304px; flex: none;
    display: flex;
  }
  .stat-men { width: 420px; background: var(--dark); }
  .stat-women { width: 420px; background: var(--green); }
  .stat-number {
    position: absolute; top: 50px;
    font-family: "Montserrat", sans-serif; font-weight: 700;
    font-size: 148px; line-height: 1; letter-spacing: -5px;
    color: var(--paper);
  }
  .stat-number.men { left: 74px; }
  .stat-number.women { left: 478px; }
  .ribbons { position: absolute; left: 0; top: 211px; width: 840px; height: 71px; }
  .ribbon-label {
    position: absolute; top: 211px; height: 71px;
    display: flex; align-items: center;
    font-family: "Montserrat", sans-serif; font-weight: 600;
    font-size: 46px; color: var(--paper); letter-spacing: -0.5px;
  }
  .ribbon-label.men { left: 190px; }
  .ribbon-label.women { left: 486px; }
  .gap-lg { height: 24px; flex: none; }
  .gap-sm { height: 13px; flex: none; }
  .band {
    flex: none; display: flex; flex-direction: column;
    justify-content: center; align-items: center; text-align: center;
    font-family: "Lato", sans-serif; color: var(--paper);
  }
  .band-dark { background: var(--dark); }
  .band-green { background: var(--green); }
  .band-intro { height: 126px; font-size: 26px; font-weight: 300; line-height: 1.3; }
  .band-truth { height: 155px; }
  .truth-title { font-weight: 700; font-size: 54px; line-height: 1.05; }
  .truth-line { font-weight: 400; font-size: 27px; }
  .band-answers { height: 125px; font-size: 27px; font-weight: 300; line-height: 1.25; }
  .conversation {
    flex: 1; display: flex; flex-direction: column;
    justify-content: center; align-items: center; text-align: center;
    font-family: "Lato", sans-serif; padding: 0 40px;
  }
  .conversation-text {
    font-weight: 700; font-size: 42px; line-height: 1.25; color: var(--green);
  }
  .conversation-rule {
    width: 560px; height: 3px; margin-top: 26px;
    background: linear-gradient(to right, transparent, var(--rule) 12%, var(--rule) 88%, transparent);
  }
</style>
</head>
<body>
<div class="sign">
  <div class="sign-inner">
    <section class="stats">
      <div class="stat-men"></div>
      <div class="stat-women"></div>
      <div class="stat-number men">50%</div>
      <div class="stat-number women">25%</div>
      <svg class="ribbons" viewBox="0 0 840 71" aria-hidden="true">
        <polygon points="63,0 420,0 420,71 8,71" fill="#4ca26f"/>
        <polygon points="420,0 776,0 829,71 420,71" fill="#262626"/>
      </svg>
      <div class="ribbon-label men">of Men</div>
      <div class="ribbon-label women">of Women</div>
    </section>
    <div class="gap-lg"></div>
    <section class="band band-dark band-intro">
      <p>Suffer From Hair Loss But Most Are In Denial That It Is<br>Happening Or Too Embarrassed To Talk About It.</p>
    </section>
    <div class="gap-sm"></div>
    <section class="band band-green band-truth">
      <h2 class="truth-title">The Truth is...</h2>
      <p class="truth-line">73% of people believe their hair is thinning They are right</p>
    </section>
    <div class="gap-sm"></div>
    <section class="band band-dark band-answers">
      <p>If you've got questions,<br>your stylist or barber has answers</p>
    </section>
    <section class="conversation">
      <p class="conversation-text">This sign has been placed here<br>to spark conversation<br>about hair loss.</p>
      <div class="conversation-rule"></div>
    </section>
  </div>
</div>
</body>
</html>
```